Web Design for Two by Two Organic Soap Company

We need a website design for the company Brevin Organics based on the package design per attached.

The design should communicate high end, luxury organic. The site will provide facts about how the spread of disease causes deaths and can be prevented with hand washing. The site will also have a page about why we are passionate about organics and how that relates to our skin including skin facts.
Also, the site should have an e-commerce product page and shopping cart.

Target Market(s)

Educated, health conscious and socially conscious consumers who shop luxury. Target vendors include Marlow Grocers and Tavelli..

Industry/Entity Type

E-Commerce

Font styles to use
Other font styles liked:
• See attached

Requirements
Must have
• Use of Ying Yang leaf Logo provided.
Based on design provided.

```html
<!DOCTYPE html>
<html lang="en">
<head>
<meta charset="utf-8">
<title>Brevin Organics – Organic Soap</title>
<link rel="stylesheet" href="https://fonts.googleapis.com/css2?family=Ubuntu:wght@400;500&family=Ubuntu+Condensed&family=Yanone+Kaffeesatz:wght@400&family=Special+Elite&display=swap">
<style>
:root{
  --page:#cfb28f;
  --dark:#2f2011;
  --nav:#3a2b1a;
  --rust:#a5391f;
  --cream:#f3e6cf;
  --panel:#d7c4ab;
  --body-text:#6b5b4b;
  --link:#4a3826;
  --accent:#e2a35f;
  --orange:#e0853e;
}
*{box-sizing:border-box;margin:0;padding:0}
html,body{width:1200px;height:1160px;overflow:hidden}
body{background:var(--page);font-family:"Ubuntu",sans-serif;position:relative;color:var(--link)}
.abs{position:absolute}

.brand-mark{left:101px;top:15px;width:72px;height:105px;background:var(--rust)}
.brand-name{left:176px;top:15px;width:241px;height:46px;background:var(--dark);color:var(--cream);font-family:"Ubuntu Condensed","Arial Narrow",sans-serif;font-size:33px;line-height:46px;padding:0 10px;white-space:nowrap;overflow:hidden}
.brand-tag{left:189px;top:72px;font-family:"Ubuntu",sans-serif;font-size:31px;line-height:40px;color:var(--dark);letter-spacing:1px;white-space:nowrap}

.account{left:690px;top:47px;font-size:13.5px;display:flex;color:var(--link);white-space:nowrap}
.account span{margin-right:27px}
.account .total{color:#c0301a;font-weight:400}

.main-nav{left:101px;top:127px;width:1000px;height:40px;background:var(--nav);display:flex}
.main-nav a{color:#fff;text-decoration:none;font-size:15px;line-height:42px;letter-spacing:.5px;display:block;text-align:center}
.main-nav .active{background:var(--rust)}

.hero{left:101px;top:168px;width:1000px;height:385px;overflow:hidden;border-bottom:3px solid var(--dark)}
.hero-photo{position:absolute;inset:0;background:linear-gradient(90deg,#5e4433 0%,#6f5440 35%,#7a5a40 62%,#e7a060 72%,#f0b46a 86%,#e89850 100%)}
.hero-curve{position:absolute;left:0;top:0}
.hero-badge{position:absolute;left:808px;top:22px;width:172px;height:172px;border-radius:50%;border:5px solid #fff;background:#c0452a}
.hero-claim{position:absolute;left:0;width:490px;top:294px;text-align:center;color:#fff;font-family:"Yanone Kaffeesatz",sans-serif;font-size:35px;line-height:36px;letter-spacing:1px;white-space:nowrap}
.hero-order{position:absolute;left:637px;top:297px;font-family:"Yanone Kaffeesatz",sans-serif;font-size:26px;color:#1a120a;white-space:nowrap}
.hero-cause{position:absolute;left:575px;top:335px;width:400px;text-align:center;font-family:"Yanone Kaffeesatz",sans-serif;font-size:18px;line-height:18px;letter-spacing:.6px;color:#1a120a;white-space:nowrap}

.sidebar{left:100px;top:578px;width:217px;height:415px;background:var(--dark)}
.sidebar h2{position:absolute;left:25px;top:16px;font-size:19px;font-weight:500;color:var(--accent)}
.shop-list{position:absolute;left:25px;top:53px;list-style:none}
.shop-list li{font-size:11.5px;color:var(--cream);line-height:21px}
.rule{position:absolute;left:15px;width:185px;height:1px;background:#4a3a28}
.social{position:absolute;left:20px;top:203px;display:flex;gap:25px}
.social span{width:22px;height:22px;border-radius:50%;background:#8a6a4a}
.cards{position:absolute;left:38px;top:275px;display:flex;gap:6px}
.cards span{width:40px;height:25px;background:#e8e2d8}
.seal{position:absolute;left:38px;top:315px;width:122px;height:31px;background:#e8e2d8}

.intro{left:341px;top:578px;width:759px;height:212px;background:var(--panel);padding:17px 16px 0}
.intro h1{font-size:25px;font-weight:400;color:#2e2012;padding-bottom:6px;border-bottom:1px dashed #8a7560;letter-spacing:.3px}
.intro p{margin-top:16px;font-size:12px;line-height:21px;color:var(--body-text)}

.offer{top:813px;width:239px;height:181px;border:1px solid var(--cream);text-align:center;font-family:"Special Elite","Courier New",monospace;color:var(--cream);overflow:hidden}
.offer.rust{background:var(--rust)}
.offer.dark{background:var(--dark)}
.offer .big{font-size:56px;line-height:62px;margin-top:10px}
.offer .item{font-size:26px;line-height:28px}
.offer .price{font-size:27px;line-height:32px;color:var(--orange);display:inline-block;border-bottom:3px solid var(--orange);margin-top:4px}
.offer .note{font-size:18px;line-height:22px;margin-top:8px}
.offer .note.small{font-size:14px;line-height:16px;margin-top:6px}

.footer-rule{left:99px;width:999px;border-top:1px dashed #8a7560}
.footer-nav{left:369px;top:1070px;font-size:14px;color:var(--link);letter-spacing:.5px;white-space:nowrap}
.footer-nav .sep{margin:0 12px}
.footer-mark{left:800px;top:1041px;width:48px;height:72px;background:var(--rust)}
</style>
</head>
<body>

<header>
  <div class="abs brand-mark"></div>
  <div class="abs brand-name">Brevin Organics</div>
  <div class="abs brand-tag">organic soap</div>
  <div class="abs account"><span>Login</span><span>0 Item(s) &nbsp;( <b class="total">$0.00</b> )</span><span>view cart</span><span>checkout</span></div>
  <nav class="abs main-nav">
    <a style="width:129px">HOME</a>
    <a class="active" style="width:127px">ABOUT</a>
    <a style="width:157px">CONTACT</a>
    <a style="width:132px">STORES</a>
    <a style="width:170px">NATURAL SOAP</a>
  </nav>
</header>

<section class="abs hero">
  <div class="hero-photo" role="img" aria-label="Handmade organic soap bars stacked on dark weathered wood beside a blurred orange floral backdrop"></div>
  <svg class="hero-curve" width="1000" height="385" viewBox="0 0 1000 385">
    <path d="M615 0 C650 60 700 120 670 230 C640 320 560 360 460 385 L490 385 C590 360 680 310 700 220 C720 120 660 50 640 0 Z" fill="#a5391f"/>
  </svg>
  <div class="hero-badge" role="img" aria-label="Close-up of an essential oil bottle"></div>
  <div class="hero-claim">Suitable For Face ,Hair and Skin<br>Scented with Organic Essential Oils</div>
  <div class="hero-order">order online brevinorganics.com</div>
  <div class="hero-cause">we are giving soap to help prevent the spread of disease;<br>1.4 million death a year can be prevented by hand washing</div>
</section>

<aside class="abs sidebar">
  <h2>shop online</h2>
  <ul class="shop-list">
    <li>organic bar soaps</li>
    <li>castile liquid soaps</li>
    <li>organic balms &amp; oils</li>
    <li>unique handmade gifts</li>
    <li>timber &amp; coal for men</li>
  </ul>
  <div class="rule" style="top:180px"></div>
  <div class="social"><span></span><span></span><span></span><span></span></div>
  <div class="rule" style="top:245px"></div>
  <div class="cards"><span></span><span></span><span></span></div>
  <div class="seal"></div>
  <div class="rule" style="top:383px"></div>
</aside>

<main>
  <section class="abs intro">
    <h1>100% real... natural, handmade, organic</h1>
    <p>Lorem ipsum dolor sit amet, consectetur adipisicing elit, sed do eiusmod tempor incididunt ut labore et dolore magna aliqua. Ut enim ad minim veniam, quis nostrud exercitation ullamco laboris nisi ut aliquip ex ea commodo consequat. Duis aute irure dolor in reprehenderit in voluptate velit esse cillum dolore eu fugiat nulla pariatur. Excepteur sint occaecat cupidatat non proident, sunt in culpa qui officia deserunt mollit anim id est laborum.Lorem ipsum dolor sit amet, consectetur adipisicing elit, sed do eiusmod tempor incididunt ut labore et dolore magna aliqua. Ut enim ad minim veniam, quis nostrud exercitation ullamco laboris nisi ut aliquip ex ea commodo consequat. Duis aute irure dolor in reprehenderit .</p>
  </section>

  <div class="abs offer rust" style="left:341px">
    <div class="big">free</div><div class="item">3 oz bar</div><div class="price">$25 order</div><div class="note">(our choice)</div>
  </div>
  <div class="abs offer dark" style="left:602px">
    <div class="big">3free</div><div class="item">3 oz bars</div><div class="price">$50 order</div><div class="note">(our choice)</div>
  </div>
  <div class="abs offer dark" style="left:863px">
    <div class="big">free</div><div class="item">shipping</div><div class="price">$75 order</div><div class="note small">(continental U.S.<br>ground,our choice)</div>
  </div>
</main>

<footer>
  <div class="abs footer-rule" style="top:1031px"></div>
  <div class="abs footer-nav">home<span class="sep">|</span>about<span class="sep">|</span>contact<span class="sep">|</span>stores<span class="sep">|</span>natural soap</div>
  <div class="abs footer-mark"></div>
  <div class="abs footer-rule" style="top:1127px"></div>
</footer>

</body>
</html>
```